professional business card design for technology company

We are a small technology consulting firm, specialising in consulting based around Cloud and Managed services. Our colour scheme is yellow, blue and white, as you can see in the logos. Although we are based in melbourne australia, due to the nature of our work, our clients can be located anywhere. We are looking for a clean, professional, positive look - similar to our company logo

Target Market(s)

small business

Industry/Entity Type

Business

Contact Information for Business Card

eye catching, designed to incorporate some level of raised printing. Must contain website address, phone number, name and job title

Requirements
Must have
• Logo (attached) - use of the same colour scheme

```html
<!DOCTYPE html>
<html lang="en">
<head>
<meta charset="utf-8">
<title>Nubivale Business Card</title>
<link rel="stylesheet" href="https://fonts.googleapis.com/css2?family=Open+Sans:wght@400;600&display=swap">
<style>
  :root {
    --page-bg: #3a3633;
    --card-bg: #141414;
    --brand-blue: #4cc3f0;
    --brand-yellow: #f3d21b;
    --text-light: #e6e6e6;
    --wordmark-grey: #5c5c5c;
    --divider: #2e2e2e;
  }
  * { margin: 0; padding: 0; box-sizing: border-box; }
  html, body {
    width: 1200px;
    height: 844px;
    overflow: hidden;
    background: var(--page-bg);
    font-family: "Open Sans", Arial, sans-serif;
  }
  .stage {
    width: 1200px;
    height: 844px;
    display: flex;
    align-items: center;
    justify-content: center;
    gap: 60px;
  }
  .card {
    width: 525px;
    height: 300px;
    background: var(--card-bg);
    position: relative;
    box-shadow: 0 10px 30px rgba(0,0,0,0.45);
  }
  /* Contact side */
  .card-contact {
    display: flex;
    align-items: center;
  }
  .brand-block {
    width: 215px;
    display: flex;
    align-items: center;
    justify-content: center;
    gap: 10px;
  }
  .brand-dot {
    width: 14px;
    height: 14px;
    border-radius: 50%;
    background: var(--brand-yellow);
  }
  .brand-name {
    font-size: 24px;
    font-weight: 600;
    color: var(--brand-blue);
  }
  .divider {
    width: 1px;
    height: 170px;
    background: var(--divider);
  }
  .details {
    padding-left: 24px;
    color: var(--text-light);
    font-size: 13px;
    line-height: 1.35;
  }
  .person-name {
    font-size: 20px;
    font-weight: 600;
    color: var(--brand-blue);
    line-height: 1.2;
  }
  .person-title {
    font-size: 12px;
    margin-bottom: 16px;
  }
  .contact-list { list-style: none; margin-bottom: 14px; }
  .contact-label { color: var(--brand-blue); }
  .address { font-size: 13px; }
  /* Brand side */
  .card-brand {
    display: flex;
    align-items: center;
    justify-content: center;
    gap: 14px;
  }
  .card-brand .brand-dot { width: 22px; height: 22px; }
  .wordmark {
    font-size: 44px;
    font-weight: 600;
    color: var(--wordmark-grey);
  }
</style>
</head>
<body>
  <main class="stage">
    <section class="card card-contact" aria-label="Business card, contact side">
      <div class="brand-block">
        <span class="brand-dot"></span>
        <span class="brand-name">Nubivale</span>
      </div>
      <div class="divider"></div>
      <div class="details">
        <p class="person-name">Liam Carter</p>
        <p class="person-title">Managing Director</p>
        <ul class="contact-list">
          <li><span class="contact-label">T:</span> 044-987 654 321</li>
          <li><span class="contact-label">E:</span> hello@nubivale.com</li>
          <li><span class="contact-label">W:</span> www.nubivale.com</li>
        </ul>
        <p class="address">48 Harbour Lane, Suite 5<br>Melbourne VIC, 3000.</p>
      </div>
    </section>
    <section class="card card-brand" aria-label="Business card, brand side">
      <span class="brand-dot"></span>
      <span class="wordmark">Nubivale</span>
    </section>
  </main>
</body>
</html>
```